Test and Tag business card design

We are an appliance test and tag company in Brisbane Australia requiring a business card design.
I don't have a logo.
Card front: Matte black background with white font.
Card back: White background with black font colour
Examples are attached
Minimalist design
Reason: Looking for more designs with an extreme minimal feel
Industry/Entity Type
Appliance
Contact Information for Business Card
Business name: Norvane Check and Label
Description: Onsite Electrical Testing and Tagging
Licence No. 41823
Name: Greg Palwick
Mobile: 0419 286 354
Email: greg@norvanecheckandlabel.com.au
Web: norvanecheckandlabel.com.au
Logo Text
Norvane Check and Label
Look and feel

```html
<!DOCTYPE html>
<html lang="en">
<head>
<meta charset="utf-8">
<title>Norvane Check and Label – Business Card</title>
<link href="https://fonts.googleapis.com/css2?family=Open+Sans:wght@400;600;700;800&display=swap" rel="stylesheet">
<style>
  :root {
    --stage: #e6e7e9;
    --card-dark: #231f20;
    --card-light: #ffffff;
    --ink-light: #ffffff;
    --ink-dark: #231f20;
    --shadow: rgba(0, 0, 0, 0.35);
  }
  * { margin: 0; padding: 0; box-sizing: border-box; }
  html, body {
    width: 1200px;
    height: 1000px;
    overflow: hidden;
    background: var(--stage);
    font-family: "Open Sans", Arial, sans-serif;
  }
  .stage { position: relative; width: 1200px; height: 1000px; }

  .card {
    position: absolute;
    width: 701px;
    height: 405px;
    box-shadow: 3px 4px 5px var(--shadow);
  }
  .card--front { left: 112px; top: 68px; background: var(--card-dark); color: var(--ink-light); }
  .card--back  { left: 388px; top: 527px; background: var(--card-light); color: var(--ink-dark); }

  .brand { position: absolute; }
  .brand__licence { font-size: 11px; line-height: 1; margin-bottom: 6px; }
  .brand__name {
    font-size: 38px;
    font-weight: 700;
    letter-spacing: -1px;
    line-height: 1;
    white-space: nowrap;
  }
  .brand__tagline {
    font-size: 9.5px;
    font-weight: 600;
    letter-spacing: 0.6px;
    margin-top: 3px;
    white-space: nowrap;
  }
  .card--front .brand { left: 38px; top: 74px; }
  .card--back .brand {
    left: 0; right: 0; top: 170px;
    text-align: center;
  }

  .contact { position: absolute; left: 38px; top: 296px; font-size: 14.5px; line-height: 22px; }
  .contact__name {
    font-size: 16px;
    font-weight: 800;
    letter-spacing: 1.2px;
    text-transform: uppercase;
    margin-bottom: 1px;
  }
  .web { position: absolute; font-size: 14.5px; line-height: 22px; white-space: nowrap; }
  .card--front .web { right: 41px; top: 339px; }
  .card--back .web { left: 0; right: 0; top: 340px; text-align: center; }
</style>
</head>
<body>
<main class="stage">
  <section class="card card--front" aria-label="Card front">
    <div class="brand">
      <p class="brand__licence">Licence No. 41823</p>
      <p class="brand__name">Norvane Check and Label</p>
      <p class="brand__tagline">ONSITE ELECTRICAL TESTING &amp; TAGGING</p>
    </div>
    <div class="contact">
      <p class="contact__name">Greg Palwick</p>
      <p>P: 0419 286 354</p>
      <p>E: greg@norvanecheckandlabel.com.au</p>
    </div>
    <p class="web">W: www.norvanecheckandlabel.com.au</p>
  </section>

  <section class="card card--back" aria-label="Card back">
    <div class="brand">
      <p class="brand__name">Norvane Check and Label</p>
      <p class="brand__tagline">ONSITE ELECTRICAL TESTING &amp; TAGGING</p>
    </div>
    <p class="web">www.norvanecheckandlabel.com.au</p>
  </section>
</main>
</body>
</html>
```